Indy Film Production Company/Studio

We need a business card designed from an existing logo. We are a digital studio/production company that caters to creating genre entertainment, like Action, Horror, and martial arts. The card along with the logo will be used to Brand the company from letter heads to banners. The design will also be used for postcards and Brochures. It should be professional and masculine.
Updates

Thank you to all the designers who have participated. I'm narrowing down who it will be. Thank you again.

Target Market(s)

Investors, Networks, Producers, and actors

Industry/Entity Type

Film Production

Contact Information for Business Card

Teodoro Valbuena
Producer/Writer/Director
www.kestrelpicturehouse.example

Requirements
Must have
• Website address, Facebook icon and Twitter icon possibly in the back of the card.
Nice to have
• Logline of Company: Follow The Action.

```html
<!DOCTYPE html>
<html lang="en">
<head>
<meta charset="utf-8">
<title>Kestrel Picture House – Business Card</title>
<link href="https://fonts.googleapis.com/css2?family=Montserrat:ital,wght@0,800;1,800&family=Roboto:wght@400&display=swap" rel="stylesheet">
<style>
  :root {
    --backdrop: #b3b1b2;
    --card-dark: #2d2a29;
    --card-light: #f4f4f3;
    --brand-red: #d2302a;
    --ink: #1d1d1d;
    --ink-soft: #2b2b2b;
    --ink-light: #d9d6d4;
    --band-dark: #262424;
  }
  * { margin: 0; padding: 0; box-sizing: border-box; }
  html, body { width: 1200px; height: 1200px; overflow: hidden; }
  body {
    position: relative;
    background: var(--backdrop);
    font-family: "Roboto", Arial, sans-serif;
    color: var(--ink);
  }
  .card { position: absolute; width: 713px; height: 418px; }

  /* Front */
  .card-front {
    left: 238px; top: 118px;
    background: var(--card-dark);
    display: flex; align-items: center; justify-content: center;
  }
  .wordmark {
    font-family: "Montserrat", Arial, sans-serif;
    font-weight: 800;
    color: var(--brand-red);
    text-transform: uppercase;
    line-height: 1;
  }
  .card-front .wordmark { text-align: center; }
  .wordmark .word-main { display: block; font-size: 66px; letter-spacing: 1px; }
  .wordmark .word-sub { display: block; font-size: 21px; letter-spacing: 0.5px; margin-top: 14px; }

  .social-row {
    position: absolute; left: 0; right: 0; bottom: 34px;
    display: flex; justify-content: center; gap: 34px;
    list-style: none;
  }
  .social-row li {
    display: flex; align-items: center; gap: 9px;
    font-size: 15px; color: var(--ink-light);
  }
  .social-dot {
    width: 14px; height: 14px; border-radius: 50%;
    background: var(--brand-red);
  }

  /* Back */
  .card-back {
    left: 230px; top: 645px;
    background: var(--card-light);
    overflow: hidden;
  }
  .card-back .wordmark { position: absolute; left: 38px; top: 76px; }
  .card-back .wordmark .word-main { font-size: 60px; }
  .card-back .wordmark .word-sub { font-size: 19px; margin-top: 26px; }

  .divider {
    position: absolute; left: 38px; top: 253px;
    width: 482px; height: 2px; background: var(--brand-red);
  }

  .identity { position: absolute; right: 33px; top: 198px; text-align: right; }
  .identity .person-name {
    font-family: "Montserrat", Arial, sans-serif;
    font-style: italic; font-weight: 800;
    font-size: 25px; color: var(--ink);
  }
  .identity .person-role { font-size: 16px; color: var(--ink-soft); margin-top: 8px; }

  .address {
    position: absolute; right: 33px; top: 294px;
    text-align: right; font-size: 17.5px; line-height: 29px; color: var(--ink-soft);
  }

  .contact-list { position: absolute; left: 38px; top: 282px; list-style: none; }
  .contact-list li {
    display: flex; align-items: center;
    font-size: 18px; height: 27.5px; color: var(--ink-soft);
  }
  .contact-list svg { width: 16px; height: 16px; margin-right: 19px; fill: var(--brand-red); }

  .band-dark {
    position: absolute; left: 0; bottom: 0;
    width: 400px; height: 22px; background: var(--band-dark);
  }
  .band-red {
    position: absolute; right: 0; bottom: 0;
    width: 340px; height: 44px; background: var(--brand-red);
    clip-path: polygon(22px 0, 100% 0, 100% 100%, 0 100%);
  }
</style>
</head>
<body>
  <section class="card card-front">
    <div class="wordmark">
      <span class="word-main">Kestrel</span>
      <span class="word-sub">Kestrel Picture House</span>
    </div>
    <ul class="social-row">
      <li><span class="social-dot" aria-hidden="true"></span>/kestrelpicturehouse</li>
      <li><span class="social-dot" aria-hidden="true"></span>@kestrelpictures</li>
    </ul>
  </section>

  <section class="card card-back">
    <div class="wordmark">
      <span class="word-main">Kestrel</span>
      <span class="word-sub">Kestrel Picture House</span>
    </div>

    <div class="identity">
      <p class="person-name">Teodoro Valbuena</p>
      <p class="person-role">Producer/Writer/Director</p>
    </div>

    <div class="divider"></div>

    <ul class="contact-list">
      <li>
        <svg viewBox="0 0 16 16" aria-hidden="true"><path d="M2 5c0-2 2-3 6-3s6 1 6 3v1h-3V4.5H5V6H2zM4 7h8l2 6v1H2v-1zm4 1.5a2 2 0 1 0 0 4 2 2 0 0 0 0-4z"/></svg>
        5550194827
      </li>
      <li>
        <svg viewBox="0 0 16 16" aria-hidden="true"><path d="M8 1a7 7 0 1 0 0 14A7 7 0 0 0 8 1zm0 1.5c.8 0 1.8 1.7 2 4.3H6c.2-2.6 1.2-4.3 2-4.3zm-2.3.5C5 4.2 4.6 5.4 4.5 6.8H2.6A5.5 5.5 0 0 1 5.7 3zm4.6 0a5.5 5.5 0 0 1 3.1 3.8h-1.9c-.1-1.4-.5-2.6-1.2-3.8zM2.6 8.3h1.9c.1 1.4.5 2.6 1.2 3.8a5.5 5.5 0 0 1-3.1-3.8zm3.4 0h4c-.2 2.6-1.2 4.3-2 4.3s-1.8-1.7-2-4.3zm5.5 0h1.9a5.5 5.5 0 0 1-3.1 3.8c.7-1.2 1.1-2.4 1.2-3.8z"/></svg>
        www.kestrelpicturehouse.example
      </li>
      <li>
        <svg viewBox="0 0 16 16" aria-hidden="true"><path d="M1 3h14v10H1zm1.5 1.2v.3L8 8.6l5.5-4.1v-.3zm0 2.1v5.2h11V6.3L8 10.4z"/></svg>
        teodoro@kestrelpicturehouse.example
      </li>
    </ul>

    <p class="address">Your Long Commercial or<br>business address in 2 line</p>

    <div class="band-dark"></div>
    <div class="band-red"></div>
  </section>
</body>
</html>
```